Tallowfield Air Business Card Design

Design new, 2 sides, business cards for a residential and light commercial heating, air conditioning contractor.

Target Market(s)

Homeowners, small businesses

Industry/Entity Type

Business

Contact Information for Business Card

Dominic Westerhall
Phone - 862-415-2736
Email
Address - PO box 518
Brightwater NJ 07912
Website - www.HarborBreezeLLC.example

Requirements
Must have
• logo, company colors, standard size with no die cut, so I can use nova stamp

```html
<!DOCTYPE html>
<html lang="en">
<head>
<meta charset="utf-8">
<title>Tallowfield Air Business Card</title>
<link rel="stylesheet" href="https://fonts.googleapis.com/css2?family=Open+Sans:ital,wght@0,400;0,600;0,700;1,400&display=swap">
<style>
  :root {
    --maroon: #9b1f32;
    --orange: #f28a2e;
    --white: #ffffff;
    --ink: #2b2b2b;
    --backdrop: #dcdcdc;
  }
  * { box-sizing: border-box; margin: 0; padding: 0; }
  html, body { width: 1105px; height: 1200px; overflow: hidden; }
  body {
    background: var(--backdrop);
    font-family: "Open Sans", Arial, sans-serif;
    position: relative;
  }
  .card {
    position: absolute;
    left: 196px;
    width: 720px;
    height: 413px;
    background: var(--white);
    border-radius: 18px;
    overflow: hidden;
  }
  .card--front { top: 145px; }
  .card--back { top: 602px; }

  .wave { position: absolute; inset: 0; width: 720px; height: 413px; }

  .brand-name {
    position: absolute;
    color: var(--maroon);
    font-weight: 700;
    white-space: nowrap;
  }
  .card--front .brand-name {
    left: 40px; width: 290px; top: 120px;
    text-align: center;
    font-size: 34px;
  }
  .card--back .brand-name {
    left: 0; right: 0; top: 165px;
    text-align: center;
    font-size: 56px;
  }

  .person {
    position: absolute;
    right: 39px; top: 132px;
    text-align: right;
    color: var(--white);
  }
  .person__name { font-size: 22px; font-weight: 700; line-height: 28px; }
  .person__title { font-size: 18px; line-height: 25px; }

  .contacts {
    position: absolute;
    right: 35px; top: 193px;
    list-style: none;
    color: var(--white);
    font-size: 17px;
  }
  .contacts li {
    display: flex; align-items: center; justify-content: flex-end;
    height: 27.5px;
  }
  .contacts svg { width: 18px; height: 18px; margin-left: 18px; fill: var(--white); }

  .address {
    position: absolute;
    right: 39px; top: 333px;
    text-align: right;
    color: var(--white);
    font-size: 17px;
    line-height: 26px;
    font-style: normal;
  }

  .tagline {
    position: absolute;
    left: 0; right: 0; top: 328px;
    text-align: center;
    color: var(--ink);
    font-size: 18px;
    font-style: italic;
    line-height: 25px;
  }
</style>
</head>
<body>

<section class="card card--front" aria-label="Business card front">
  <svg class="wave" viewBox="0 0 720 413" aria-hidden="true">
    <path fill="var(--orange)" d="M0,330 C130,322 240,232 340,158 C420,100 500,70 590,62 L720,60 L720,66 C600,66 500,82 350,160 C250,236 140,326 0,358 Z"/>
    <path fill="var(--maroon)" stroke="var(--white)" stroke-width="3" d="M0,370 C150,330 260,232 360,156 C450,92 560,64 722,62 L722,415 L0,415 Z"/>
  </svg>

  <div class="brand-name">Tallowfield Air</div>

  <div class="person">
    <div class="person__name">DOMINIC WESTERHALL</div>
    <div class="person__title">CEO/Founder</div>
  </div>

  <ul class="contacts">
    <li>862 415 2736
      <svg viewBox="0 0 24 24" aria-hidden="true"><path d="M6.6 10.8a15 15 0 0 0 6.6 6.6l2.2-2.2c.3-.3.7-.4 1-.2 1.1.4 2.3.6 3.6.6.6 0 1 .4 1 1V20c0 .6-.4 1-1 1C10.6 21 3 13.4 3 4c0-.6.4-1 1-1h3.5c.6 0 1 .4 1 1 0 1.3.2 2.5.6 3.6.1.3 0 .7-.2 1z"/></svg>
    </li>
    <li>862 415 2741
      <svg viewBox="0 0 24 24" aria-hidden="true"><path d="M7 2h10a2 2 0 0 1 2 2v16a2 2 0 0 1-2 2H7a2 2 0 0 1-2-2V4a2 2 0 0 1 2-2zm0 3v13h10V5zm5 14.2a1 1 0 1 0 0 .01z"/></svg>
    </li>
    <li>862 415 2759
      <svg viewBox="0 0 24 24" aria-hidden="true"><path d="M6 2h12v6H6zM3 9h18a1 1 0 0 1 1 1v8h-4v4H6v-4H2v-8a1 1 0 0 1 1-1zm5 7v4h8v-4z"/></svg>
    </li>
    <li>dominic@tallowfieldair.example
      <svg viewBox="0 0 24 24" aria-hidden="true"><path d="M2 5h20v14H2zm2 2v.5l8 5 8-5V7l-8 5z"/></svg>
    </li>
    <li>www.TallowfieldAirLLC.example
      <svg viewBox="0 0 24 24" aria-hidden="true"><path d="M12 2a10 10 0 1 0 0 20 10 10 0 0 0 0-20zm-1 17.9A8 8 0 0 1 4.1 11H7c.2 2 .7 3.8 1.6 5.2zM13 4.1a8 8 0 0 1 6.9 6.9H17c-.3-2.9-1.5-5-4-6.9zM11 9H8.5c.4-2 1.2-3.6 2.5-4.8zm2 2h2c-.2 2.6-1 5-2 6.5zm4 2h2.9a8 8 0 0 1-4.7 6.2c1-1.7 1.6-3.8 1.8-6.2z"/></svg>
    </li>
  </ul>

  <address class="address">
    PO box 518<br>
    Brightwater NJ 07912
  </address>
</section>

<section class="card card--back" aria-label="Business card back">
  <div class="brand-name">Tallowfield Air</div>
  <p class="tagline">
    Residential &amp; light commercial heating<br>
    Air conditioning contractor
  </p>
</section>

</body>
</html>
```